A weight loss and fitness website design

I am into different types of modern weight loss techniques for people who are a little fatty and wish to be physically and mentally fit. Basically, the website is to teach people how to reduce weight using different methods such as diet, exercises, yoga and other forms. I would need an eye catching website which would make visitors want to come back. The will be also be different forms of exercises for a health and fit life. This said, my website is to have two categories of
1) weight loss techniques
2) exercise of fit and healthy living.
I prefer bright colors such as green, blue, yellow, and orange. Imagery should include before and after pictures of people suffering from obesity, people under going exercises.
Designers can get ideas and inspiration from the website fitlumen.com which i was previously part of the team.
Target Market(s)
My target audience are people suffering from obesity, malnutrition and physical deficiency.
Industry/Entity Type
Fitness
Coding
Coded - Design and coding required
Number of Pages Required
1 page
Look and feel

```html
<!DOCTYPE html>
<html lang="en">
<head>
<meta charset="utf-8">
<title>Brightstep Fitness</title>
<link rel="stylesheet" href="https://fonts.googleapis.com/css2?family=Oswald:wght@500;600;700&family=Raleway:ital,wght@0,400;0,600;0,700;1,400&display=swap">
<style>
:root{
  --green:#4f9b12;
  --blue:#2262c6;
  --blue-dark:#1d57b3;
  --yellow:#f6ea1c;
  --orange:#f8a21a;
  --white:#ffffff;
  --text:#555555;
  --footer:#3f3f3f;
  --line:#e6e6e6;
}
*{box-sizing:border-box;margin:0;padding:0}
html,body{width:1200px;height:3719px;overflow:hidden;background:var(--white)}
body{font-family:"Raleway",Arial,sans-serif;color:var(--text);position:relative}
section,header,footer{position:absolute;left:0;width:1200px}
.abs{position:absolute}
h2{font-family:"Oswald",Arial,sans-serif;font-weight:600;font-size:25px;letter-spacing:.5px;text-transform:uppercase}
.center{text-align:center}
.btn{position:absolute;display:flex;align-items:center;justify-content:center;font-family:"Raleway",sans-serif;font-weight:700;font-size:13px;text-transform:uppercase;color:var(--white);background:var(--orange);letter-spacing:.3px}
p.body{font-size:13.5px;line-height:23px}

/* header */
.site-header{top:0;height:82px;background:var(--white)}
.brand{left:75px;top:22px;font-family:"Oswald",sans-serif;font-weight:700;font-size:30px;color:var(--blue);letter-spacing:.5px}
.main-nav{right:72px;top:34px;display:flex;gap:34px;font-size:12px;font-weight:700;text-transform:uppercase;color:#444}
.main-nav .active{color:var(--blue)}

/* hero */
.hero{top:82px;height:533px;background:linear-gradient(180deg,#7f9aa6 0%,#c7c09a 30%,#8a8a6a 55%,#3a3a32 78%,#2a2a26 100%)}
.hero-title{top:222px;width:100%;text-align:center;font-family:"Oswald",sans-serif;font-weight:700;font-size:64px;color:var(--yellow);letter-spacing:1px}
.hero-sub{top:308px;width:100%;text-align:center;font-weight:700;font-size:16px;line-height:24px;color:var(--white);text-transform:uppercase}
.dots{top:488px;left:570px;display:flex;gap:10px}
.dots span{width:8px;height:8px;border-radius:50%;background:var(--white)}
.dots span:first-child{background:var(--yellow)}

/* welcome */
.welcome{top:615px;height:322px}
.welcome h2{color:var(--blue-dark);position:absolute;top:38px;width:100%}
.welcome p{position:absolute;left:75px;width:1050px;top:94px;text-align:center}

/* what we do */
.what{top:937px;height:434px;background:var(--green)}
.what h2{color:var(--white);left:75px;top:80px;position:absolute}
.what p{position:absolute;left:75px;top:132px;width:605px;color:var(--white)}
.btn-outline{background:transparent;border:2px solid var(--yellow)}
.video{left:704px;top:57px;width:421px;height:320px;background:linear-gradient(135deg,#cfc7bd,#8f8477 60%,#b3a898)}
.play{left:868px;top:170px}

/* how to teach */
.teach{top:1371px;height:431px}
.teach h2{color:var(--blue-dark);position:absolute;top:40px;width:100%}
.teach .lead{position:absolute;top:102px;width:100%;font-size:13.5px}
.feature{position:absolute;top:156px;width:340px;text-align:center}
.feature .icon{margin:0 auto;width:84px;height:84px;border:2px solid var(--blue);display:flex;align-items:center;justify-content:center}
.feature h3{margin-top:26px;font-size:15px;font-weight:700;color:var(--orange);text-transform:uppercase}
.feature p{margin-top:6px;font-size:13.5px;line-height:22px}

/* categories */
.categories{top:1802px;height:652px;background:var(--green)}
.category{position:absolute;top:0;width:513px;text-align:center}
.category h2{color:var(--yellow);margin-top:52px;font-size:25px}
.category .photo{margin-top:20px;height:268px}
.category p{margin:22px auto 0;width:470px;color:var(--white)}

/* before after */
.results{top:2454px;height:521px}
.results h2{color:var(--blue-dark);position:absolute;top:38px;width:100%}
.results .lead{position:absolute;top:96px;width:100%;font-size:13.5px}
.compare{top:144px;width:513px;height:322px;background:linear-gradient(90deg,#eeeeee,#f7f7f7 50%,#eeeeee)}
.tag{position:absolute;left:198px;width:154px;height:44px;display:flex;align-items:center;justify-content:center;gap:8px;color:var(--white);font-weight:700;font-size:14px;text-transform:uppercase}
.tag.before{top:122px;background:var(--blue)}
.tag.after{top:179px;background:var(--orange)}
.slide-arrow{position:absolute}

/* testimonials */
.testimonials{top:2975px;height:322px;background:var(--green)}
.testimonials h2{color:var(--white);position:absolute;top:30px;width:100%}
.avatar{left:136px;top:96px;width:154px;height:154px;border-radius:50%;background:linear-gradient(160deg,#dfe6ee,#9fb0c2);border:4px solid var(--white)}
.quote{left:342px;top:100px;width:755px;font-style:italic;color:var(--white);font-size:13.5px;line-height:22px}
.quote-name{left:342px;top:222px;font-weight:700;font-style:italic;color:var(--yellow);font-size:13px}

/* contact band */
.contact{top:3297px;height:236px;background:var(--blue)}
.contact h3{position:absolute;top:50px;font-family:"Oswald",sans-serif;font-weight:600;font-size:22px;color:var(--white);text-transform:uppercase;letter-spacing:.5px}
.email-field{left:75px;top:99px;width:329px;height:45px;background:var(--white);font-size:11px;font-weight:600;color:#555;padding-left:14px;display:flex;align-items:center;text-transform:uppercase}
.signup{left:293px;top:154px;width:111px;height:45px;border:2px solid var(--white);background:transparent;font-size:12px}
.contact-line{left:466px;display:flex;align-items:center;gap:14px;color:var(--yellow);font-weight:700}
.socials{left:833px;top:92px;display:grid;grid-template-columns:repeat(3,40px);gap:14px 17px}
.socials span{width:40px;height:40px;border:2px solid var(--yellow);border-radius:50%}

/* footer */
.site-footer{top:3533px;height:186px;background:var(--footer)}
.foot-nav{top:67px;width:100%;display:flex;justify-content:center;gap:28px;font-size:12px;text-transform:uppercase;color:var(--white)}
.copyright{top:104px;width:100%;text-align:center;font-size:12px;color:#cfcfcf}
</style>
</head>
<body>

<header class="site-header">
  <div class="abs brand">BRIGHTSTEP FITNESS</div>
  <nav class="abs main-nav">
    <span class="active">Home</span><span>About Us</span><span>Teach</span><span>Services</span><span>Before &amp; After</span><span>Testimonials</span><span>Contact Us</span>
  </nav>
</header>

<section class="hero" role="img" aria-label="Men sprinting along a road at sunset">
  <div class="abs hero-title">BRIGHTSTEP FITNESS</div>
  <div class="abs hero-sub">We provide modern weight loss techniques for people who are a little<br>fatty and wish to be physically and mentally fit.</div>
  <div class="abs dots"><span></span><span></span><span></span><span></span></div>
</section>

<section class="welcome">
  <h2 class="center">Welcome to our website</h2>
  <p class="body">Aliquam molestie, mi et imperdiet euismod, dui purus auctor tellus, et interdum lacus lectus et ante. Sed accumsan sollicitudin sapien, sit amet adipiscing turpis gravida ac. In congue, neque ac lobortis volutpat, libero mauris varius mi, vitae suscipit ipsum ligula vitae risus. Duis aliquam nibh a dui iaculis viverra id a velit. Vivamus egestas risus in magna varius commodo. Sed semper viverra egestas. Etiam pretium porttitor lectus, vel ornare neque porta volutpat.</p>
  <div class="btn" style="left:523px;top:233px;width:154px;height:45px">Read More</div>
</section>

<section class="what">
  <h2>What we do</h2>
  <p class="body">Aliquam molestie, mi et imperdiet euismod, dui purus auctor tellus, et interdum lacus lectus et ante. Sed accumsan sollicitudin sapien, sit amet adipiscing turpis gravida ac. In congue, neque ac lobortis volutpat, libero mauris varius mi, vitae suscipit ipsum ligula vitae risus. Duis aliquam nibh a dui iaculis viverra id a velit. Vivamus egestas risus in magna varius commodo.</p>
  <div class="btn" style="left:75px;top:303px;width:153px;height:47px">Read More</div>
  <div class="btn btn-outline" style="left:240px;top:303px;width:235px;height:47px">Book an Appointment</div>
  <div class="abs video" role="img" aria-label="Group exercise class doing squats in a gym"></div>
  <svg class="abs play" width="92" height="92" viewBox="0 0 92 92"><circle cx="46" cy="46" r="22" fill="none" stroke="#fff" stroke-width="5"/><path d="M40 35 L57 46 L40 57 Z" fill="#fff"/></svg>
</section>

<section class="teach">
  <h2 class="center">How to teach</h2>
  <div class="lead center">Aliquam molestie, mi et imperdiet euismod, dui purus auctor tellus, et interdum lacus lectus et ante.</div>
  <div class="feature" style="left:70px">
    <div class="icon"><svg width="46" height="46" viewBox="0 0 46 46" fill="none" stroke="#333" stroke-width="2.5"><rect x="9" y="7" width="28" height="34" rx="2"/><rect x="17" y="3" width="12" height="7" fill="#fff"/><path d="M14 19l3 3 5-6M14 31l3 3 5-6M26 20h7M26 32h7"/></svg></div>
    <h3>Proper Diet Chart</h3>
    <p>Sed accumsan sollicitudin sapien, sit amet adipiscing turpis gravida ac. In congue, neque ac lobortis volutpat libero.</p>
  </div>
  <div class="feature" style="left:428px">
    <div class="icon"><svg width="46" height="46" viewBox="0 0 46 46" fill="none" stroke="#333" stroke-width="2.5" stroke-linecap="round"><circle cx="22" cy="9" r="4" fill="#333"/><path d="M22 14l-2 12 8 14M20 26l-8 10M21 17l10-8M21 18l-9 3"/></svg></div>
    <h3>Physical Exercises</h3>
    <p>Sed accumsan sollicitudin sapien, sit amet adipiscing turpis gravida ac. In congue, neque ac lobortis volutpat libero.</p>
  </div>
  <div class="feature" style="left:790px">
    <div class="icon"><svg width="46" height="46" viewBox="0 0 46 46" fill="none" stroke="#333" stroke-width="2.5" stroke-linecap="round"><circle cx="23" cy="9" r="4" fill="#333"/><path d="M23 14v13M23 18l-10 7M23 18l10 7M8 35c6-5 24-5 30 0M10 38h26"/></svg></div>
    <h3>Yoga</h3>
    <p>Sed accumsan sollicitudin sapien, sit amet adipiscing turpis gravida ac. In congue, neque ac lobortis volutpat libero.</p>
  </div>
</section>

<section class="categories">
  <div class="category" style="left:75px">
    <h2>Weight Loss Techniques</h2>
    <div class="photo" role="img" aria-label="Woman exercising on a mat in a gym" style="background:linear-gradient(135deg,#d8d8d6,#a9a9a6 55%,#c64a4a)"></div>
    <p class="body">Aliquam molestie, mi et imperdiet euismod, dui purus auctor tellus, et interdum lacus lectus et ante. Sed accumsan sollicitudin sapien, sit amet adipiscing turpis gravida ac. In congue, neque ac lobortis volutpat, libero mauris varius mi, vitae suscipit ipsum ligula vitae risus.</p>
    <div class="btn" style="left:180px;top:543px;width:154px;height:48px">Read More</div>
  </div>
  <div class="category" style="left:615px">
    <h2>Exercise of Fit and Healthy Living</h2>
    <div class="photo" role="img" aria-label="Woman seated on the floor lifting dumbbells" style="background:linear-gradient(135deg,#f3f3f1,#cfcac4 55%,#ebe8e4)"></div>
    <p class="body">Aliquam molestie, mi et imperdiet euismod, dui purus auctor tellus, et interdum lacus lectus et ante. Sed accumsan sollicitudin sapien, sit amet adipiscing turpis gravida ac. In congue, neque ac lobortis volutpat, libero mauris varius mi, vitae suscipit ipsum ligula vitae risus.</p>
    <div class="btn" style="left:180px;top:543px;width:154px;height:48px">Read More</div>
  </div>
</section>

<section class="results">
  <h2 class="center">Before and after</h2>
  <div class="lead center">Aliquam molestie, mi et imperdiet euismod, dui purus auctor tellus, et interdum lacus lectus et ante.</div>
  <svg class="slide-arrow" style="left:42px;top:286px" width="16" height="30" viewBox="0 0 16 30"><path d="M14 2L2 15l12 13" fill="none" stroke="#444" stroke-width="2.5"/></svg>
  <svg class="slide-arrow" style="left:1140px;top:286px" width="16" height="30" viewBox="0 0 16 30"><path d="M2 2l12 13L2 28" fill="none" stroke="#444" stroke-width="2.5"/></svg>
  <div class="abs compare" style="left:75px" role="img" aria-label="Man shown before and after weight loss">
    <div class="tag before"><svg width="14" height="12" viewBox="0 0 14 12"><path d="M13 6H2M6 1L1 6l5 5" fill="none" stroke="#fff" stroke-width="2.2"/></svg>Before</div>
    <div class="tag after">After<svg width="14" height="12" viewBox="0 0 14 12"><path d="M1 6h11M8 1l5 5-5 5" fill="none" stroke="#fff" stroke-width="2.2"/></svg></div>
  </div>
  <div class="abs compare" style="left:615px" role="img" aria-label="Woman shown before and after weight loss">
    <div class="tag before"><svg width="14" height="12" viewBox="0 0 14 12"><path d="M13 6H2M6 1L1 6l5 5" fill="none" stroke="#fff" stroke-width="2.2"/></svg>Before</div>
    <div class="tag after">After<svg width="14" height="12" viewBox="0 0 14 12"><path d="M1 6h11M8 1l5 5-5 5" fill="none" stroke="#fff" stroke-width="2.2"/></svg></div>
  </div>
</section>

<section class="testimonials">
  <h2 class="center">Testimonials</h2>
  <svg class="slide-arrow" style="left:78px;top:138px" width="14" height="26" viewBox="0 0 14 26"><path d="M12 2L2 13l10 11" fill="none" stroke="#fff" stroke-width="2.5"/></svg>
  <svg class="slide-arrow" style="left:1110px;top:138px" width="14" height="26" viewBox="0 0 14 26"><path d="M2 2l10 11L2 24" fill="none" stroke="#fff" stroke-width="2.5"/></svg>
  <div class="abs avatar" role="img" aria-label="Portrait of a smiling client"></div>
  <div class="abs quote">" Aliquam molestie, mi et imperdiet euismod, dui purus auctor tellus, et interdum lacus lectus et ante. Sed accumsan sollicitudin sapien, sit amet adipiscing turpis gravida ac. In congue, neque ac lobortis volutpat, libero mauris varius mi, vitae suscipit ipsum ligula vitae risus. Duis aliquam nibh a dui iaculis viverra id a velit. Vivamus egestas risus in magna varius commodo."</div>
  <div class="abs quote-name">-Name Heading</div>
</section>

<section class="contact">
  <h3 style="left:75px">Sign Up Newsletter</h3>
  <div class="abs email-field">Enter email address</div>
  <div class="btn signup">Sign Up</div>

  <h3 style="left:466px">Contact Us</h3>
  <div class="abs contact-line" style="top:96px;font-size:24px">
    <svg width="22" height="22" viewBox="0 0 22 22"><rect x="1" y="1" width="20" height="20" rx="4" fill="#f6ea1c"/><path d="M7 5c-1 1-2 2 0 6s5 6 7 6c1 0 2-1 2-2l-2-2-2 1c-1 0-3-2-3-3l1-2-2-3z" fill="#2262c6"/></svg>
    1-800-555-0142
  </div>
  <div class="abs contact-line" style="top:148px;font-size:17px">
    <svg width="24" height="18" viewBox="0 0 24 18"><rect x="1" y="1" width="22" height="16" rx="2" fill="#f6ea1c"/><path d="M2 3l10 7 10-7" fill="none" stroke="#2262c6" stroke-width="2"/></svg>
    info@brightstepfit.com
  </div>

  <h3 style="left:826px">Follow Us</h3>
  <div class="abs socials"><span></span><span></span><span></span><span></span><span></span><span></span></div>
</section>

<footer class="site-footer">
  <nav class="abs foot-nav"><span>Home</span><span>About Us</span><span>Teach</span><span>Services</span><span>Before &amp; After</span><span>Testimonials</span><span>Contact Us</span></nav>
  <div class="abs copyright">Copyright © 2016. Company Name All Right Reserved</div>
</footer>

</body>
</html>
```